Web Design Project for Orvane Ridge Advisors, LP

We are looking for a new website for Orvane Ridge Advisors, LP an investment management (alternative investment) firm with offices in New York, NY and Seattle, WA. We are looking for designs utilizing gray, blue and white, corresponding with our logo. Our current website is www.orvaneridgellc.example.

Some websites with the feel we are looking for:

http://pelvorholdings.example/cgi-bin/index.pl
http://www.quillbrooklp.example/

Target Market(s)

wealthy individuals and large investors

Industry/Entity Type

Investment

Requirements
Must have
• A couple/few page website, utilizing the below text & contact info and use one of the logos that are attached.

Text to be inlcuded:

Orvane Ridge Advisors, LP is a hedge fund manager responsible for a multi-strategy fund primarily implementing a long/short equity strategy and utilizing macro, credit, event driven and distressed strategies while maintaining a market neutral portfolio.

The Fund seeks to achieve absolute returns while minimizing risk with particular attention paid to preserving capital.

Contact information to be included:

East Coast:

417 Harlow Street #738
New York, NY 10027
Phone : +1 212.555.0147
Fax : +1 212.555.0183
info@orvaneridgellc.example

West Coast:

3748 Fenwick Lane #526
Seattle, WA 98134
info@orvaneridgellc.example
Should not have
• anything too flashy

```html
<!DOCTYPE html>
<html lang="en">
<head>
<meta charset="utf-8">
<title>Orvane Ridge Advisors, LP</title>
<link rel="stylesheet" href="https://fonts.googleapis.com/css2?family=Tinos:wght@400;700&display=swap">
<style>
  :root {
    --navy: #2f5077;
    --navy-dark: #284669;
    --button: #25426a;
    --ink: #2e2e2e;
    --muted: #666a70;
    --line: #d6d6d6;
    --bubble: #f1f1f1;
    --white: #ffffff;
  }
  * { margin: 0; padding: 0; box-sizing: border-box; }
  html, body { width: 1200px; height: 872px; overflow: hidden; background: var(--white); }
  body { position: relative; font-family: "Tinos", "Times New Roman", serif; color: var(--ink); }

  .bubble { position: absolute; border-radius: 50%; }
  .bubble--top { left: -60px; top: -200px; width: 390px; height: 325px; background: radial-gradient(circle, #f6f6f6 60%, #fbfbfb 100%); }
  .bubble--right { left: 920px; top: 105px; width: 520px; height: 400px; background: radial-gradient(ellipse at 40% 50%, #f3f3f3 0%, #f7f7f7 55%, rgba(255,255,255,0) 72%); }
  .bubble--low { left: -200px; top: 470px; width: 480px; height: 460px; background: radial-gradient(circle at 50% 55%, #e9e9e9 0%, #eeeeee 45%, rgba(255,255,255,0) 72%); }
  .bubble--dot1 { left: 422px; top: 99px; width: 74px; height: 72px; background: #f6f6f6; }
  .bubble--dot2 { left: 471px; top: 92px; width: 47px; height: 45px; background: #f3f3f3; }
  .bubble--dot3 { left: 790px; top: 166px; width: 24px; height: 24px; background: #f1f1f1; }

  .header { position: absolute; left: 236px; top: 140px; width: 724px; height: 56px; }
  .brand { position: absolute; left: 0; top: 8px; font-size: 27px; color: var(--navy); letter-spacing: 0.5px; white-space: nowrap; }
  .contact { position: absolute; right: 0; top: 12px; font-size: 13px; line-height: 18px; color: var(--muted); }

  .nav-band { position: absolute; left: 0; top: 199px; width: 1200px; height: 42px; background: linear-gradient(#3a5b82, var(--navy-dark)); }
  .nav { position: absolute; left: 238px; top: 0; display: flex; gap: 37px; list-style: none; height: 42px; align-items: center; }
  .nav a { position: relative; color: var(--white); text-decoration: none; font-size: 13.5px; letter-spacing: 0.3px; }
  .nav .is-current::after { content: ""; position: absolute; left: 17px; top: 25px; border: 5px solid transparent; border-bottom-color: var(--white); }
  .search { position: absolute; left: 804px; top: 8px; width: 156px; height: 26px; background: var(--white); display: flex; align-items: center; padding: 0 10px; font-size: 11px; color: #7a7a7a; justify-content: space-between; }

  .portrait { position: absolute; left: 235px; top: 271px; width: 170px; height: 170px; border-radius: 50%; background: var(--white); box-shadow: 0 3px 10px rgba(0,0,0,0.25); padding: 5px; }
  .portrait span { display: block; width: 100%; height: 100%; border-radius: 50%; background: radial-gradient(circle at 45% 30%, #8a5a3e 0%, #9d7458 28%, #d49a5a 48%, #8fb2d8 62%, #6e95c4 100%); }

  .welcome { position: absolute; left: 427px; top: 263px; font-size: 23px; font-weight: 400; color: #55585c; }
  .welcome strong { color: var(--navy); font-weight: 700; }
  .intro { position: absolute; left: 430px; top: 304px; width: 388px; height: 163px; border-top: 1px solid var(--line); border-right: 1px solid var(--line); }
  .intro p { position: absolute; left: -1px; top: 14px; width: 380px; font-size: 13.5px; line-height: 21.2px; color: var(--ink); }
  .read-more { position: absolute; left: 259px; top: 112px; width: 78px; height: 29px; background: var(--button); color: var(--white); font-size: 13px; font-weight: 700; text-align: center; line-height: 28px; text-decoration: none; }
  .read-more::after { content: ""; position: absolute; left: 34px; bottom: 0; border: 4px solid transparent; border-bottom-color: var(--white); }

  .footer-line { position: absolute; left: 0; top: 466px; width: 1200px; height: 47px; border-top: 1px solid var(--line); border-bottom: 1px solid var(--line); }
  .footer { position: absolute; left: 235px; top: 466px; width: 740px; height: 47px; border-left: 1px solid var(--line); border-right: 1px solid var(--line); display: flex; align-items: center; justify-content: space-between; padding: 0 16px 0 17px; font-size: 13px; color: var(--muted); }
  .footer strong { color: var(--navy); }
  .footer-links { display: flex; gap: 17px; list-style: none; }
  .footer-links a { color: #888; text-decoration: none; }
  .footer-links .is-current a { color: #444; }
</style>
</head>
<body>
  <div class="bubble bubble--top"></div>
  <div class="bubble bubble--right"></div>
  <div class="bubble bubble--low"></div>
  <div class="bubble bubble--dot1"></div>
  <div class="bubble bubble--dot2"></div>
  <div class="bubble bubble--dot3"></div>

  <header class="header">
    <div class="brand">Orvane Ridge Advisors, LP</div>
    <div class="contact">Phone : +1 212.555.0147<br>info@orvaneridgellc.example</div>
  </header>

  <nav class="nav-band">
    <ul class="nav">
      <li><a class="is-current" href="#">HOME</a></li>
      <li><a href="#">ABOUT ORVANE</a></li>
      <li><a href="#">TEAM</a></li>
      <li><a href="#">NEWS</a></li>
      <li><a href="#">GALLERY</a></li>
      <li><a href="#">CONTACT</a></li>
    </ul>
    <div class="search">
      <span>Search your phrase...</span>
      <svg width="14" height="14" viewBox="0 0 14 14" aria-hidden="true"><circle cx="5.5" cy="5.5" r="4.2" fill="none" stroke="#666" stroke-width="2"/><line x1="8.6" y1="8.6" x2="12.6" y2="12.6" stroke="#666" stroke-width="2.4" stroke-linecap="round"/></svg>
    </div>
  </nav>

  <div class="portrait"><span role="img" aria-label="Portrait photo of a smiling advisor in a blue shirt in an office"></span></div>

  <h1 class="welcome">Welcome to <strong>Orvane Ridge</strong></h1>
  <section class="intro">
    <p>Orvane Ridge Advisors, LP is a hedge fund manager responsible for a multi-strategy fund primarily implementing a long/short equity strategy and utilizing macro, credit, event driven and distressed strategies while maintaining a market neutral portfolio...</p>
    <a class="read-more" href="#">read more</a>
  </section>

  <div class="footer-line"></div>
  <footer class="footer">
    <span>Copyright by <strong>ORVANE RIDGE</strong>. All rights reserved.</span>
    <ul class="footer-links">
      <li class="is-current"><a href="#">Home</a></li>
      <li><a href="#">Site map</a></li>
      <li><a href="#">Privacy Policy</a></li>
    </ul>
  </footer>
</body>
</html>
```